Looking for a website that shows the services available to customers.This company will provide consulting on how to reduce costs and improve overal IT spend within any organization. We will employ experts in many aspects of IT including Cloud, Mainframe, ZR720/oFrame/TFrame, Disaster Recovery, IT optimization strategies, Colocation, Hybrid IT, Migrations, Networking, Security etc. I am a technology advisor that helps to optimize costs in IT

Target Market(s)

Al companies over $1M in revenue

Industry/Entity Type

It Company

Number of Pages Required

5+ page

Font styles to use
Serif
Sans Serif

Requirements
Must have
• Tabs for: About us (our team), Services, Why Solvanta, Testimonials, Contact Us
Nice to have
• i would like to have on my services pages some logos of partners. Such as quellbyte, K&L, etc.

I need an understanding of how to add/change to the website
Should not have
• no spirlay fonts or any thing scrolly. I want t professional IT website

```html
<!DOCTYPE html>
<html lang="en">
<head>
<meta charset="utf-8">
<title>Solvanta – IT Cost Optimization Consulting</title>
<link rel="stylesheet" href="https://fonts.googleapis.com/css2?family=Lexend:wght@300;400;500;600&family=Poppins:ital,wght@0,300;0,400;0,500;0,600;1,400&display=swap">
<style>
:root{
  --navy:#0a1524;
  --navy-2:#0d1c2c;
  --green:#8dc63f;
  --teal:#2bb3a3;
  --blue:#2a5aa8;
  --blue-2:#2597c8;
  --ink:#14171c;
  --muted:#7d838c;
  --pale:#f4f7fc;
  --white:#ffffff;
}
*{margin:0;padding:0;box-sizing:border-box}
html,body{width:1200px;height:4202px;overflow:hidden}
body{position:relative;background:var(--white);font-family:"Poppins",sans-serif;color:var(--ink)}
.abs{position:absolute}
h1,h2,h3,.head{font-family:"Lexend",sans-serif;font-weight:500}
.underline{position:absolute;height:3px;width:80px}
.underline::before{content:"";position:absolute;left:0;top:0;width:58px;height:3px;background:var(--blue)}
.underline::after{content:"";position:absolute;left:62px;top:0;width:6px;height:3px;background:var(--blue);box-shadow:10px 0 0 var(--blue)}
.btn{position:absolute;background:var(--green);color:#fff;font-family:"Lexend",sans-serif;font-size:13px;font-weight:500;display:flex;align-items:center;justify-content:center;border-radius:8px;letter-spacing:.2px}
.photo{position:absolute}

/* header + hero */
.hero-bg{left:0;top:0;width:1200px;height:675px;background:radial-gradient(ellipse at 20% 90%,#0f2a38 0%,var(--navy) 60%)}
.brand{left:161px;top:50px;color:#fff;font-family:"Lexend",sans-serif;font-size:26px;font-weight:500;display:flex;align-items:center;gap:8px}
.brand .dot{width:12px;height:12px;border-radius:50%;background:var(--teal)}
.tagline{left:161px;top:86px;color:#cdd5de;font-size:5.5px;letter-spacing:.3px}
.nav{left:420px;top:36px;display:flex;gap:20px;font-size:11px;color:#cdd5de}
.nav .active{color:var(--green);position:relative}
.nav .active::before{content:"";position:absolute;left:50%;top:-16px;width:1px;height:10px;background:var(--green)}
.nav .active::after{content:"";position:absolute;left:calc(50% - 3px);top:-8px;width:5px;height:5px;border:1px solid var(--green);border-radius:50%}
.phone-top{left:898px;top:32px;color:#fff;font-family:"Lexend",sans-serif;font-size:16px;font-weight:500;display:flex;align-items:center;gap:8px}
.hero-photo{left:404px;top:173px;width:796px;height:580px;border-bottom-left-radius:100px;background:linear-gradient(120deg,#4d6070 0%,#8a8f8f 40%,#c99357 62%,#6d5a48 85%,#3a3d44 100%)}
.scroll-down{left:985px;top:147px;width:52px;height:52px;border-radius:50%;background:var(--teal);display:flex;align-items:center;justify-content:center}
.hero-title{left:161px;top:228px;font-family:"Lexend",sans-serif;font-size:76px;line-height:80px;font-weight:600;letter-spacing:-1px}
.hero-title .outline{color:transparent;-webkit-text-stroke:1.5px #e7ecf2;font-weight:400;display:block}
.hero-title .solid{color:#fff;display:block}
.hero-text{left:161px;top:404px;color:#dfe5ec;font-size:12.5px;line-height:24px}
.slider-dots{left:22px;top:645px;display:flex;gap:6px}
.slider-dots span{width:22px;height:2px;background:#3a4c5e}
.slider-dots span:first-child{background:var(--teal)}

/* welcome */
.welcome-bg{left:0;top:675px;width:1200px;height:585px;background:var(--pale)}
.pic{position:absolute;border:1.5px solid var(--navy)}
.welcome-kicker{left:676px;top:864px;color:var(--teal);font-size:13px}
.welcome-title{left:672px;top:884px;font-size:42px;font-weight:500}
.welcome-lead{left:672px;top:955px;width:300px;color:var(--blue);font-style:italic;font-size:11.5px;line-height:21px}
.welcome-body{left:672px;top:1027px;width:300px;color:var(--muted);font-size:11px;line-height:21px}

/* services */
.section-title{position:absolute;left:0;width:1200px;text-align:center;font-family:"Lexend",sans-serif;font-weight:500;font-size:35px;color:var(--ink)}
.service{position:absolute;width:160px;text-align:center}
.service .icon{width:72px;height:72px;border-radius:50%;margin:0 auto;display:flex;align-items:center;justify-content:center}
.service h3{font-family:"Lexend",sans-serif;font-weight:500;font-size:13px;line-height:20px;margin-top:14px;color:var(--ink)}
.service p{font-size:11px;line-height:18px;color:var(--muted);margin-top:12px}

/* question */
.question-photo{left:0;top:1867px;width:680px;height:394px;border-bottom-right-radius:40px;background:linear-gradient(100deg,#cfd3d6 0%,#e9e6e0 35%,#b9804a 55%,#d7d2cb 75%,#efefec 100%)}
.question-title{left:753px;top:1938px;font-size:32px;line-height:38px}
.call-label{left:815px;top:2052px;font-size:10px;font-weight:600}
.call-number{left:811px;top:2068px;color:var(--teal);font-family:"Lexend",sans-serif;font-size:25px;font-weight:500}

/* why */
.why-halo{left:222px;top:2392px;width:376px;height:376px;border-radius:50%;background:radial-gradient(circle,#f1f4f9 0%,#f6f8fb 60%,rgba(255,255,255,0) 72%)}
.why-photo{left:304px;top:2482px;width:244px;height:244px;border-radius:50%;background:radial-gradient(circle at 50% 45%,#e7edf3 0%,#b6bfc9 55%,#4f5863 100%)}
.why-title{left:642px;top:2402px;font-size:35px}
.checks{left:649px;top:2482px;list-style:none}
.checks li{display:flex;align-items:center;gap:14px;font-size:11.5px;color:#333;height:34px}

/* experts */
.experts-bg{left:0;top:2816px;width:1200px;height:569px;background:linear-gradient(100deg,var(--blue) 0%,#2676ba 55%,var(--blue-2) 100%)}
.experts-title{color:#fff}
.experts-sub{left:0;width:1200px;top:2954px;text-align:center;color:#dfe9f6;font-style:italic;font-size:12px;line-height:22px}
.card{position:absolute;top:3033px;width:202px;height:275px;border-radius:22px 22px 0 0;overflow:hidden;background:#3e7fc4}
.card .face{height:203px}
.card .name{text-align:center;color:#fff;font-family:"Lexend",sans-serif;font-size:16px;margin-top:18px}
.card .role{text-align:center;color:#dbe6f3;font-size:11px;margin-top:1px}

/* testimonials */
.avatar{position:absolute;width:68px;height:68px;border-radius:50%}
.quote{left:340px;top:3655px;width:520px;text-align:center;color:#555;font-size:13px;line-height:26px}
.quote .mark{color:var(--blue);font-family:"Lexend",sans-serif;font-weight:600}
.client{left:0;width:1200px;top:3752px;text-align:center;font-size:14px;color:#333}
.t-dots{left:560px;top:3795px;display:flex;gap:5px}
.t-dots span{width:10px;height:10px;border-radius:50%;border:1px solid #aaa}
.t-dots span:first-child{background:var(--green);border-color:var(--green)}

/* footer */
.footer-bg{left:0;top:3885px;width:1200px;height:317px;background:radial-gradient(ellipse at 30% 40%,#12202f 0%,var(--navy) 70%)}
.footer-brand{left:178px;top:4042px;color:#fff;font-family:"Lexend",sans-serif;font-size:44px;font-weight:500;display:flex;align-items:center;gap:12px}
.footer-brand .dot{width:18px;height:18px;border-radius:50%;background:var(--teal)}
.f-col{position:absolute;top:3930px;color:#c7cfd8}
.f-col h4{font-family:"Lexend",sans-serif;font-weight:500;font-size:14px;color:#fff;position:relative;padding-bottom:10px}
.f-col h4::after{content:"";position:absolute;left:0;bottom:0;width:32px;height:2px;background:var(--blue-2)}
.sitemap{list-style:none;margin-top:16px}
.sitemap li{font-size:11px;height:23.5px;display:flex;align-items:center;gap:14px}
.sitemap li::before{content:"";width:5px;height:5px;background:var(--green)}
.contact-row{display:flex;gap:14px;align-items:flex-start;font-size:10.5px;line-height:16px}
.email-field{position:absolute;left:836px;top:3954px;width:202px;height:34px;border-radius:10px;background:#fff;color:#888;font-size:10px;padding-left:18px;display:flex;align-items:center}
.subscribe{left:836px;top:3996px;width:202px;height:36px;border-radius:10px;font-size:13px}
.socials{left:893px;top:4073px;display:flex;gap:22px}
.socials span{width:14px;height:14px;border-radius:50%;background:#fff}
.divider{left:161px;top:4152px;width:878px;height:1px;background:#1f2d3c}
.copyright{left:0;width:1200px;top:4171px;text-align:center;color:var(--green);font-size:10px}
.copyright span{color:#c7cfd8}
</style>
</head>
<body>

<!-- Header & hero -->
<div class="abs hero-bg"></div>
<div class="photo hero-photo" role="img" aria-label="Hand placing coins on a stack beside a glowing light bulb"></div>
<div class="abs scroll-down"><svg width="22" height="14" viewBox="0 0 22 14"><path d="M3 4l8 7 8-7" fill="none" stroke="#fff" stroke-width="2"/></svg></div>
<div class="abs brand"><span class="dot"></span>Solvanta</div>
<div class="abs tagline">A SMART PATH TO IT SAVINGS</div>
<nav class="abs nav">
  <span class="active">Home</span><span>About Us</span><span>Services</span><span>Why Solvanta</span><span>Testimonials</span><span>Contact Us</span>
</nav>
<div class="abs phone-top">
  <svg width="18" height="18" viewBox="0 0 24 24"><path d="M6.6 10.8a15.2 15.2 0 006.6 6.6l2.2-2.2c.3-.3.7-.4 1-.2 1.1.4 2.3.6 3.6.6.6 0 1 .4 1 1V20c0 .6-.4 1-1 1A17 17 0 013 4c0-.6.4-1 1-1h3.5c.6 0 1 .4 1 1 0 1.2.2 2.4.6 3.6.1.3 0 .7-.2 1l-2.3 2.2z" fill="var(--green)"/></svg>
  555 014 2290
</div>
<h1 class="abs hero-title"><span class="outline">LEAD WITH</span><span class="solid">CONFIDENCE</span></h1>
<div class="underline" style="left:161px;top:385px"></div>
<p class="abs hero-text">Will Provide Consulting On How To Reduce Costs And<br>Improve Overal IT Spend Within Any Organization.</p>
<div class="btn" style="left:161px;top:470px;width:209px;height:39px">GET STARTED WITH US</div>
<div class="abs slider-dots"><span></span><span></span><span></span></div>

<!-- Welcome -->
<div class="abs welcome-bg"></div>
<div class="pic" style="left:215px;top:840px;width:193px;height:257px;background:linear-gradient(160deg,#a7b4c0,#5b6f86)" role="img" aria-label="Consultant smiling on a phone call"></div>
<div class="pic" style="left:416px;top:840px;width:168px;height:205px;background:linear-gradient(160deg,#c9ccd0,#8b8378)" role="img" aria-label="Team shaking hands in a meeting"></div>
<div class="pic" style="left:235px;top:1107px;width:226px;height:78px;background:linear-gradient(100deg,#4c5a6a,#c9a58a)" role="img" aria-label="Colleagues discussing work at a desk"></div>
<div class="pic" style="left:470px;top:1052px;width:114px;height:133px;background:linear-gradient(160deg,#d6d9dc,#8e7b6d)" role="img" aria-label="Woman thinking at her laptop"></div>
<div class="abs welcome-kicker">Welcome To</div>
<h2 class="abs welcome-title">Solvanta</h2>
<div class="underline" style="left:674px;top:939px"></div>
<p class="abs welcome-lead">Lorem Ipsum is simply dummy text of the Text printing and typesetting industry. Lorem Ipsum has been the industry's text print.</p>
<p class="abs welcome-body">Lorem Ipsum is simply dummy text of the printing and typesetting industry. Lorem Ipsum has been the industry's standard dummy text ever since the 1500s, when an unknown printer.</p>
<div class="btn" style="left:675px;top:1127px;width:142px;height:39px">LEARN MORE</div>

<!-- Services -->
<h2 class="section-title" style="top:1328px">Services We Provide</h2>
<div class="underline" style="left:429px;top:1378px"></div>

<div class="service" style="left:158px;top:1422px"><div class="icon" style="background:#eef7e6"><svg width="38" height="26" viewBox="0 0 38 26"><path d="M9 24h21a7 7 0 000-14 10 10 0 00-19-1A7.5 7.5 0 009 24z" fill="none" stroke="var(--green)" stroke-width="1.6"/></svg></div><h3>Cloud</h3><p>Lorem Ipsum is simply<br>dummy text.</p></div>
<div class="service" style="left:337px;top:1422px"><div class="icon" style="background:#e6f6f3"><svg width="30" height="36" viewBox="0 0 30 36"><rect x="2" y="2" width="26" height="32" rx="2" fill="none" stroke="var(--teal)" stroke-width="1.6"/><path d="M7 9h16M7 14h16M7 19h16M7 24h16M7 29h16" stroke="var(--teal)" stroke-width="1.4"/></svg></div><h3>Mainframe</h3><p>Lorem Ipsum is simply<br>dummy text.</p></div>
<div class="service" style="left:517px;top:1422px"><div class="icon" style="background:#e8ebf6"><svg width="34" height="34" viewBox="0 0 34 34"><rect x="3" y="3" width="28" height="8" rx="2" fill="none" stroke="#3a4fa0" stroke-width="1.5"/><rect x="3" y="13" width="28" height="8" rx="2" fill="none" stroke="#3a4fa0" stroke-width="1.5"/><rect x="3" y="23" width="28" height="8" rx="2" fill="none" stroke="#3a4fa0" stroke-width="1.5"/><circle cx="8" cy="7" r="1.3" fill="#3a4fa0"/><circle cx="8" cy="17" r="1.3" fill="#3a4fa0"/><circle cx="8" cy="27" r="1.3" fill="#3a4fa0"/></svg></div><h3>ZR720/oFrame/<br>TFrame</h3><p style="margin-top:8px">Lorem Ipsum is simply<br>dummy text.</p></div>
<div class="service" style="left:698px;top:1422px"><div class="icon" style="background:#e5f3f5"><svg width="36" height="34" viewBox="0 0 36 34"><path d="M4 30h28M10 30V18h16v12M18 4v8M12 8l6-5 6 5" fill="none" stroke="#1f8a9a" stroke-width="1.6"/><circle cx="18" cy="23" r="3" fill="none" stroke="#1f8a9a" stroke-width="1.4"/></svg></div><h3>Disaster Recovery</h3><p>Lorem Ipsum is simply<br>dummy text.</p></div>
<div class="service" style="left:880px;top:1422px"><div class="icon" style="background:#f6e8f1"><svg width="34" height="32" viewBox="0 0 34 32"><rect x="3" y="3" width="28" height="20" rx="2" fill="none" stroke="#a8327a" stroke-width="1.6"/><path d="M12 29h10M17 23v6" stroke="#a8327a" stroke-width="1.6"/><circle cx="17" cy="13" r="5" fill="none" stroke="#a8327a" stroke-width="1.4"/></svg></div><h3>IT Optimization<br>Strategies</h3><p style="margin-top:8px">Lorem Ipsum is simply<br>dummy text.</p></div>

<div class="service" style="left:158px;top:1642px"><div class="icon" style="background:#eef7e6"><svg width="36" height="36" viewBox="0 0 36 36"><circle cx="18" cy="18" r="6" fill="none" stroke="var(--green)" stroke-width="1.6"/><path d="M18 3v8M18 25v8M3 18h8M25 18h8M7 7l6 6M23 23l6 6M29 7l-6 6M7 29l6-6" stroke="var(--green)" stroke-width="1.4"/></svg></div><h3>Colocation</h3><p style="margin-top:0">Lorem Ipsum is simply<br>dummy text.</p></div>
<div class="service" style="left:337px;top:1642px"><div class="icon" style="background:#e5eef7"><svg width="36" height="32" viewBox="0 0 36 32"><rect x="3" y="3" width="30" height="20" rx="2" fill="none" stroke="#2a6bb0" stroke-width="1.6"/><path d="M13 29h10M18 23v6M12 17h13a3.5 3.5 0 000-7 5 5 0 00-9-1 4 4 0 00-4 8z" fill="none" stroke="#2a6bb0" stroke-width="1.4"/></svg></div><h3>Hybrid IT</h3><p style="margin-top:0">Lorem Ipsum is simply<br>dummy text.</p></div>
<div class="service" style="left:517px;top:1642px"><div class="icon" style="background:#f4e8f2"><svg width="34" height="30" viewBox="0 0 34 30"><path d="M17 3L3 10l14 7 14-7zM3 15l14 7 14-7M3 20l14 7 14-7" fill="none" stroke="#8a3a82" stroke-width="1.5"/></svg></div><h3>Migrations</h3><p style="margin-top:0">Lorem Ipsum is simply<br>dummy text.</p></div>
<div class="service" style="left:698px;top:1642px"><div class="icon" style="background:#e5eef7"><svg width="32" height="36" viewBox="0 0 32 36"><rect x="10" y="3" width="12" height="10" fill="none" stroke="#2a6bb0" stroke-width="1.5"/><path d="M16 13v6M5 19h22M5 19v5M16 19v5M27 19v5" fill="none" stroke="#2a6bb0" stroke-width="1.5"/><rect x="2" y="24" width="7" height="8" fill="none" stroke="#2a6bb0" stroke-width="1.4"/><rect x="12.5" y="24" width="7" height="8" fill="none" stroke="#2a6bb0" stroke-width="1.4"/><rect x="23" y="24" width="7" height="8" fill="none" stroke="#2a6bb0" stroke-width="1.4"/></svg></div><h3>Networking</h3><p style="margin-top:0">Lorem Ipsum is simply<br>dummy text.</p></div>
<div class="service" style="left:880px;top:1642px"><div class="icon" style="background:#eef7e6"><svg width="30" height="34" viewBox="0 0 30 34"><path d="M15 2l12 5v9c0 8-5 13-12 16C8 29 3 24 3 16V7z" fill="none" stroke="var(--green)" stroke-width="1.6"/><path d="M10 17l4 4 7-8" fill="none" stroke="var(--green)" stroke-width="1.6"/></svg></div><h3>Security</h3><p style="margin-top:0">Lorem Ipsum is simply<br>dummy text.</p></div>

<!-- Question -->
<svg class="abs" style="left:0;top:2150px" width="1200" height="186" viewBox="0 0 1200 186"><polygon points="0,186 0,40 680,23 1200,100 1200,186" fill="var(--green)"/></svg>
<div class="photo question-photo" role="img" aria-label="Smiling consultant with arms crossed in a bright office"></div>
<h2 class="abs question-title">Have An Any<br>Question ?</h2>
<div class="underline" style="left:758px;top:2021px"></div>
<svg class="abs" style="left:757px;top:2057px" width="44" height="44" viewBox="0 0 44 44"><circle cx="22" cy="22" r="20" fill="none" stroke="var(--teal)" stroke-width="1.8"/><path d="M15 13c-1 0-2 1-2 2 0 9 7 16 16 16 1 0 2-1 2-2v-3l-4-2-2 2c-3-1-5-3-6-6l2-2-2-4z" fill="none" stroke="var(--teal)" stroke-width="1.6"/></svg>
<div class="abs call-label">Call Us On :</div>
<div class="abs call-number">555 014 2290</div>

<!-- Why -->
<div class="abs why-halo" role="img" aria-label="Soft decorative backdrop around the team photo"></div>
<div class="photo why-photo" role="img" aria-label="Team celebrating around a whiteboard"></div>
<h2 class="abs why-title">Why Solvanta</h2>
<div class="underline" style="left:649px;top:2455px"></div>
<ul class="abs checks">
  <li><svg width="18" height="14" viewBox="0 0 18 14"><path d="M2 7l5 5 9-10" fill="none" stroke="var(--teal)" stroke-width="2.4"/></svg>Lorem Ipsum is simply dummy text</li>
  <li><svg width="18" height="14" viewBox="0 0 18 14"><path d="M2 7l5 5 9-10" fill="none" stroke="var(--teal)" stroke-width="2.4"/></svg>Lorem Ipsum is text printy type industry</li>
  <li><svg width="18" height="14" viewBox="0 0 18 14"><path d="M2 7l5 5 9-10" fill="none" stroke="var(--teal)" stroke-width="2.4"/></svg>Lorem Ipsum is simply text unknown printer</li>
  <li><svg width="18" height="14" viewBox="0 0 18 14"><path d="M2 7l5 5 9-10" fill="none" stroke="var(--teal)" stroke-width="2.4"/></svg>Lorem Ipsum is simply dummy text</li>
  <li><svg width="18" height="14" viewBox="0 0 18 14"><path d="M2 7l5 5 9-10" fill="none" stroke="var(--teal)" stroke-width="2.4"/></svg>Lorem Ipsum is text type</li>
  <li><svg width="18" height="14" viewBox="0 0 18 14"><path d="M2 7l5 5 9-10" fill="none" stroke="var(--teal)" stroke-width="2.4"/></svg>Lorem Ipsum is text printy type industry</li>
</ul>
<div class="btn" style="left:634px;top:2700px;width:142px;height:39px">LEARN MORE</div>

<!-- Experts -->
<div class="abs experts-bg"></div>
<h2 class="section-title experts-title" style="top:2888px">Meet Our Experts</h2>
<div class="underline" style="left:456px;top:2936px;filter:brightness(0) invert(1)"></div>
<p class="abs experts-sub">Lorem Ipsum is simply dummy text of the Text printing and typesetting<br>industry. Lorem Ipsum has been the industry's text print.</p>
<div class="card" style="left:161px"><div class="face" style="background:linear-gradient(180deg,#e6e9ec,#9fa7b0)" role="img" aria-label="Portrait of a consultant in a dark blazer"></div><div class="name">Client Name</div><div class="role">Something.com</div></div>
<div class="card" style="left:386px"><div class="face" style="background:linear-gradient(180deg,#a6cf62,#8dc63f)" role="img" aria-label="Portrait of a consultant in a light blouse"></div><div class="name">Client Name</div><div class="role">Something.com</div></div>
<div class="card" style="left:611px"><div class="face" style="background:linear-gradient(180deg,#d9dcdf,#7c838b)" role="img" aria-label="Portrait of a consultant holding a phone"></div><div class="name">Client Name</div><div class="role">Something.com</div></div>
<div class="card" style="left:836px"><div class="face" style="background:linear-gradient(180deg,#e8e9eb,#b9b6b2)" role="img" aria-label="Portrait of a consultant in a white shirt"></div><div class="name">Client Name</div><div class="role">Something.com</div></div>

<!-- Testimonials -->
<h2 class="section-title" style="top:3456px">What Our Client Say</h2>
<div class="underline" style="left:437px;top:3506px"></div>
<div class="avatar" style="left:541px;top:3554px;background:#5b3a9a;display:flex;align-items:center;justify-content:center;color:#fff;font-family:Lexend,sans-serif;font-size:30px;font-weight:600">“</div>
<div class="avatar" style="left:587px;top:3554px;background:linear-gradient(160deg,#c7b9ae,#6a5a52);border:3px solid #fff" role="img" aria-label="Client portrait"></div>
<svg class="abs" style="left:244px;top:3672px" width="20" height="30" viewBox="0 0 20 30"><path d="M16 2L4 15l12 13" fill="none" stroke="#222" stroke-width="2.4"/></svg>
<svg class="abs" style="left:925px;top:3672px" width="20" height="30" viewBox="0 0 20 30"><path d="M4 2l12 13L4 28" fill="none" stroke="var(--teal)" stroke-width="2.4"/></svg>
<p class="abs quote"><span class="mark">“</span> Lorem Ipsum is simply dummy text of the printing and typesetting industry. Lorem Ipsum has been the industry's standard dummy text ever since the 1500s, when an unknown printer. <span class="mark">”</span></p>
<div class="abs client">– Client Name</div>
<div class="abs t-dots"><span></span><span></span><span></span><span></span><span></span></div>

<!-- Footer -->
<div class="abs footer-bg"></div>
<div class="abs footer-brand"><span class="dot"></span>Solvanta</div>

<div class="f-col" style="left:388px">
  <h4>Sitemap</h4>
  <ul class="sitemap"><li>Home</li><li>About us</li><li>Services</li><li>Why Solvanta</li><li>Testimonials</li><li>Contact Us</li></ul>
</div>

<div class="f-col" style="left:611px;width:210px">
  <h4>Contact Us</h4>
  <div class="contact-row" style="margin-top:16px"><svg width="14" height="18" viewBox="0 0 14 18"><path d="M7 1a6 6 0 00-6 6c0 4.5 6 10 6 10s6-5.5 6-10a6 6 0 00-6-6z" fill="none" stroke="var(--green)" stroke-width="1.6"/><circle cx="7" cy="7" r="2" fill="var(--green)"/></svg><div><div style="color:#fff;font-size:12px;font-family:Lexend,sans-serif">Solvanta</div>101 – Lorem ipsum simple text<br>print type text industy.</div></div>
  <div class="contact-row" style="margin-top:14px;align-items:center"><svg width="14" height="14" viewBox="0 0 24 24"><path d="M6.6 10.8a15.2 15.2 0 006.6 6.6l2.2-2.2c.3-.3.7-.4 1-.2 1.1.4 2.3.6 3.6.6.6 0 1 .4 1 1V20c0 .6-.4 1-1 1A17 17 0 013 4c0-.6.4-1 1-1h3.5c.6 0 1 .4 1 1 0 1.2.2 2.4.6 3.6.1.3 0 .7-.2 1l-2.3 2.2z" fill="var(--green)"/></svg><span style="color:#fff;font-size:13px">+(1) 555 014 2290</span></div>
  <div class="contact-row" style="margin-top:14px;align-items:center"><svg width="16" height="12" viewBox="0 0 16 12"><rect x="0" y="0" width="16" height="12" rx="1" fill="var(--green)"/><path d="M1 1l7 6 7-6" fill="none" stroke="var(--navy)" stroke-width="1.4"/></svg><span>info@solvanta-advisory.com</span></div>
</div>

<div class="f-col" style="left:836px"><h4>Newsletter Signup!</h4></div>
<div class="email-field">Enter Email *</div>
<div class="btn subscribe">SUBSCRIBE</div>
<div class="abs socials"><span></span><span></span><span></span></div>

<div class="abs divider"></div>
<div class="abs copyright">©Solvanta <span>– 2020 All Rights reserved.</span></div>

</body>
</html>
```